Klassisches Visitenkarten-Design mit braunen Farbtönen gesucht
Zielgruppe
Meine Firma bietet Pferdezahnbehandlungen, Pferdefütterungsberatung sowie Trensen- und Gebissanpassungen an. Ausserdem habe ich eine mobile Pferdewaage. Meine Kunden sind Pferdebesitzer der gehobenen Klasse, die gerne Geld in die Hand nehmen um ihr Tier korrekt zu halten/versorgen.
Ich setze bisher auf ein klassisches Design in braun Tönen.
Aufgabenstellung
Mir ist eine klare, schnörkellose Botschaft wichtig.
Ich möchte mich gerne mit klassischem, aber auch sehr schönem Design von der Konkurrenz abheben.
Der Fokus soll auf der wissenschaftlichen Arbeitsweise mit dem Partner Pferd liegen.
Im Anhang sind Fotos von der alten Visitenkarten. Dort fehlt mir aber die klare Linie.
Normalerweise arbeite ich mit der Schriftart Eurostyle, bin aber auch für neue Vorschläge offen.

```html
<!DOCTYPE html>
<html lang="de">
<head>
<meta charset="utf-8">
<title>Visitenkarte EQUIVIA – Vorder- und Rückseite</title>
<link rel="stylesheet" href="https://fonts.googleapis.com/css2?family=Exo+2:wght@300;400;700&display=swap">
<style>
  :root {
    --page-bg: #ededed;
    --card-bg: #ffffff;
    --brown-dark: #552d12;
    --text-grey: #727272;
  }
  html, body {
    margin: 0;
    padding: 0;
    width: 1200px;
    height: 1200px;
    overflow: hidden;
    background: var(--page-bg);
    font-family: "Exo 2", "Eurostile", sans-serif;
  }
  .card {
    position: absolute;
    left: 240px;
    width: 727px;
    height: 470px;
    background: var(--card-bg);
    color: var(--text-grey);
  }
  .card--front { top: 81px; }
  .card--back { top: 647px; }

  .accent-band {
    position: absolute;
    left: 0;
    top: 0;
    width: 34px;
    height: 100%;
    background: var(--brown-dark);
  }
  .contact {
    position: absolute;
    left: 51px;
    top: 96px;
    margin: 0;
  }
  .contact__name {
    margin: 0 0 20px;
    font-size: 27px;
    font-weight: 700;
    line-height: 1.1;
  }
  .contact__role {
    margin: 0 0 24px;
    font-size: 21px;
    font-weight: 700;
    line-height: 1.15;
  }
  .contact__address,
  .contact__lines {
    margin: 0 0 22px;
    font-size: 22px;
    font-weight: 300;
    line-height: 1.12;
    font-style: normal;
  }
  .services {
    position: absolute;
    margin: 0;
    font-size: 19px;
    font-weight: 700;
    white-space: nowrap;
  }
  .card--front .services { left: 51px; top: 393px; }
  .card--back .services { left: 0; right: 0; top: 408px; text-align: center; }

  .brand-mark {
    position: absolute;
    display: flex;
    align-items: center;
    gap: 12px;
    color: var(--brown-dark);
    font-weight: 700;
    font-size: 34px;
    letter-spacing: 1px;
  }
  .brand-mark__dot {
    width: 22px;
    height: 22px;
    border-radius: 50%;
    background: var(--brown-dark);
  }
  .card--front .brand-mark { left: 470px; top: 180px; }
  .card--back .brand-mark { left: 0; right: 0; top: 180px; justify-content: center; }
</style>
</head>
<body>
  <section class="card card--front">
    <div class="accent-band"></div>
    <div class="contact">
      <h1 class="contact__name">Marlene V. Hartwig</h1>
      <p class="contact__role">Agrarwissenschaften (Dr. sc.)<br>EQUIVIA</p>
      <address class="contact__address">Lindenweg 14<br>79790 Tannbach/Südschwarzwald</address>
      <p class="contact__lines">Telefon: +49 (0) 160 - 5550123<br>E-Mail: info@equivia-pferd.de<br>Internet: www.equivia.de</p>
    </div>
    <div class="brand-mark"><span class="brand-mark__dot"></span><span>EQUIVIA</span></div>
    <p class="services">Pferdezahnbehandlung * Pferdefütterungsberatung * Pferdewaage</p>
  </section>

  <section class="card card--back">
    <div class="brand-mark"><span class="brand-mark__dot"></span><span>EQUIVIA</span></div>
    <p class="services">Pferdezahnbehandlung * Pferdefütterungsberatung * Pferdewaage</p>
  </section>
</body>
</html>
```